Meridian Crestline Motors *

Professional business cards for our auto wholesale dealership.

Target Market(s)

New and used cars sales managers and middle class to higher end private party buyers.

Industry/Entity Type

Automotive

Contact Information for Business Card

Meridian Crestline Motors
Darnell R Okonski
Owner
(555) 304-6618
mercrestmotors@quillbox.example
Dealer Lic # 48265

Logo Text

Meridian Crestline Motors, Mer Crest Motors, MCM, etc

Font styles to use
Serif
Sans Serif

Colors

Designer to choose colors to be used in the design.

Requirements
Must have
• A professional, but not pretentious, look
Nice to have
• It might be nice to see "MCM" in a shape form i.e. circle, triangle, etc in the corner or background somehwere
Should not have
• bright "girly" colors

```html
<!DOCTYPE html>
<html lang="en">
<head>
<meta charset="utf-8">
<title>Meridian Crestline Motors – Business Cards</title>
<link rel="stylesheet" href="https://fonts.googleapis.com/css2?family=Lato:wght@400;700;900&display=swap">
<style>
  :root {
    --page-bg: #d6d6d6;
    --red-bright: #e4303a;
    --red-mid: #c01f27;
    --red-deep: #72100f;
    --frame-black: #111111;
    --paper: #ffffff;
    --ink: #1c1c1c;
    --ink-soft: #444444;
  }
  * { box-sizing: border-box; margin: 0; padding: 0; }
  html, body {
    width: 1200px; height: 800px; overflow: hidden;
    background: var(--page-bg);
    font-family: "Lato", Arial, sans-serif;
  }
  .sheet {
    width: 1200px; height: 800px;
    display: flex; align-items: center; justify-content: center; gap: 50px;
  }
  .card {
    position: relative;
    width: 540px; height: 309px;
    box-shadow: 0 10px 24px rgba(0,0,0,.18);
  }
  .card__frame {
    position: absolute; inset: 12px;
    border: 3px solid var(--frame-black);
    box-shadow: 0 0 0 3px var(--paper), inset 0 0 0 3px var(--paper);
  }

  /* Front */
  .card--front {
    background: linear-gradient(150deg, var(--red-bright) 0%, var(--red-mid) 45%, var(--red-deep) 100%);
  }
  .card--front .card__frame { box-shadow: 0 0 0 3px var(--paper); }
  .front__brand {
    position: absolute; inset: 0;
    display: flex; align-items: center; justify-content: center; gap: 16px;
  }
  .brand-mark {
    width: 58px; height: 58px; flex: none;
    background: var(--paper);
  }
  .brand-name {
    font-weight: 900; text-transform: uppercase;
    font-size: 26px; line-height: 1.05; letter-spacing: .04em;
    color: var(--paper);
  }

  /* Back */
  .card--back {
    background: var(--paper);
    border: 12px solid var(--red-mid);
    background-clip: padding-box;
  }
  .card--back::before {
    content: ""; position: absolute; inset: -12px;
    border: 12px solid transparent;
    background: linear-gradient(150deg, var(--red-bright), var(--red-deep)) border-box;
    -webkit-mask: linear-gradient(#000 0 0) padding-box, linear-gradient(#000 0 0);
    -webkit-mask-composite: xor; mask-composite: exclude;
  }
  .card--back .card__frame { inset: 4px; border-width: 2px; box-shadow: none; }
  .back__layout {
    position: absolute; inset: 0;
    display: flex; align-items: center; padding: 0 28px 0 36px;
  }
  .back__brand { display: flex; align-items: center; gap: 12px; width: 50%; }
  .back__brand .brand-mark { width: 44px; height: 44px; background: var(--red-mid); }
  .back__brand .brand-name { color: var(--red-mid); font-size: 19px; }
  .contact { width: 50%; text-align: center; }
  .contact__name { font-weight: 900; font-size: 22px; color: var(--red-mid); }
  .contact__role { font-size: 13px; color: var(--ink-soft); margin-bottom: 16px; }
  .contact__email { font-size: 11.5px; color: var(--ink); }
  .contact__phone { font-size: 25px; color: var(--ink); margin: 4px 0 8px; }
  .contact__license { font-size: 12px; color: var(--red-mid); }
</style>
</head>
<body>
  <main class="sheet">
    <section class="card card--front" aria-label="Business card front">
      <div class="card__frame"></div>
      <div class="front__brand">
        <span class="brand-mark"></span>
        <span class="brand-name">Meridian<br>Crestline Motors</span>
      </div>
    </section>

    <section class="card card--back" aria-label="Business card back">
      <div class="card__frame"></div>
      <div class="back__layout">
        <div class="back__brand">
          <span class="brand-mark"></span>
          <span class="brand-name">Meridian<br>Crestline<br>Motors</span>
        </div>
        <div class="contact">
          <p class="contact__name">Darnell R Okonski</p>
          <p class="contact__role">Owner</p>
          <p class="contact__email">mercrestmotors@quillbox.example</p>
          <p class="contact__phone">(555) 304-6618</p>
          <p class="contact__license">Dealer Lic # 48265</p>
        </div>
      </div>
    </section>
  </main>
</body>
</html>
```